Etiketten für junge Imkerei
Renate hat super schnell verstanden was ich mir vorstelle und auch Änderungen rasant umgesetzt. Ich werde in Zukunft auf jedenfall wieder mit Renate arbeiten.
Zielgruppe
Wir sind eine junge Imkerei, die spezielle und außergewöhnliche Honigspezialitäten vermarktet.
Ich verkaufe meine Produkte hauptsächlich auf dem Markt im direkten Kundenkontakt, dennoch wird ein Barcode benötigt da einige Produkte auch im Laden verfügbar sind. Meine Kunden sind hauptsächlich Frauen im mittleren Alter.
Heute brauche ich Etiketten für meine neuen OXYMEL (Sauerhonig) Produkte, Oxymel ist ein Arzneisaft der bereits in der Antike verwendet wurde:
- Amber Meadow (Blütenhonig, Apfelessig, Zitrone, Ingwer und Kurkuma)
- Storm Tonic (Apfelessig, Blütenhonig, Zwiebel, Ingwer, Meerrettich, Knoblauch, Senf, Zimt, Gewürznelken, Chilli, Blutorange)
- Kids (Blütenhonig, Apfelessig, Hagebutte, Holunderblüte)
Aufgabenstellung
Es soll ein Flaschenetikett werden.
Die Etikettengröße soll ungefähr 40x120 mm sein, wobei ich hier nicht auf eine genaue Rechteckige Form festgelegt bin, sondern auch gerne eine freie Form (z.B. Logo außerhalb). Dann bis max. 60mm hoch. Ich verwende die Flasche Vanta von Plumosa.
Inhalt: 200 ml.
Verwendetes Papier: Baumwollpapier
Barcode
Das Etikett soll vom Schema zu meinen anderen Etiketten passen. Es soll feminin und ein wenig verspielt sein aber edel wirken.
Es soll die Natürlichkeit wiederspiegeln aber nicht nach Arznei aussehen.
Im Anhang befinden sich 2 von meinen aktuellen Etiketten der Honige, diese werden auf Biofolie gedruckt.

```html
<!DOCTYPE html>
<html lang="de">
<head>
<meta charset="utf-8">
<title>Oxymel – Amber Meadow Etikett</title>
<link rel="stylesheet" href="https://fonts.googleapis.com/css2?family=Barlow+Condensed:ital,wght@1,700&family=Great+Vibes&family=Roboto:wght@400&display=swap">
<style>
  :root {
    --page: #ffffff;
    --label: #feeb9c;
    --pill: #fdebb9;
    --title: #5b5a57;
    --ink: #111111;
    --tulip: #f37290;
    --sunflower: #fbd347;
    --sunflower-ring: #fde79a;
    --blossom: #f7a29f;
    --stem: #17777f;
    --bee: #f9d94f;
    --bee-wing: #e4dfca;
    --daisy: #ffffff;
    --daisy-line: #111111;
  }
  * { margin: 0; padding: 0; box-sizing: border-box; }
  html, body {
    width: 1200px;
    height: 1200px;
    overflow: hidden;
    background: var(--page);
  }
  .canvas {
    position: relative;
    width: 1200px;
    height: 1200px;
  }
  .label {
    position: absolute;
    left: 48px;
    top: 61px;
    width: 1104px;
    height: 1109px;
    border-radius: 84px;
    background: var(--label);
  }
  .art { position: absolute; }

  .art--tulip {
    left: 172px; top: 211px; width: 276px; height: 276px;
    border-radius: 62% 38% 58% 42% / 48% 55% 45% 52%;
    background: radial-gradient(circle at 55% 40%, var(--tulip) 0 65%, #f47f99 100%);
  }
  .art--sunflower {
    left: 847px; top: 306px; width: 325px; height: 325px;
    border-radius: 50%;
    background: radial-gradient(circle, var(--sunflower) 0 27%, var(--sunflower-ring) 27% 33%, var(--sunflower) 33% 100%);
  }
  .art--blossom {
    left: 617px; top: 764px; width: 189px; height: 206px;
    border-radius: 46% 46% 42% 42%;
    background: var(--blossom);
  }
  .art--stem {
    left: 387px; top: 878px; width: 236px; height: 114px;
    border-radius: 30% 60% 20% 40%;
    background: linear-gradient(160deg, rgba(23,119,127,0.85), rgba(23,119,127,0.55));
  }
  .art--bee {
    width: 82px; height: 86px;
    border-radius: 50%;
    background: radial-gradient(circle at 60% 62%, var(--bee) 0 48%, var(--bee-wing) 80%, transparent 100%);
  }
  .bee-top   { left: 747px; top: 52px; }
  .bee-left  { left: 182px; top: 662px; }
  .bee-right { left: 950px; top: 792px; }

  .art--daisy {
    width: 52px; height: 52px;
    border-radius: 50%;
    background: var(--daisy);
    border: 3px solid var(--daisy-line);
  }
  .daisy-1 { left: 30px;   top: 189px; }
  .daisy-2 { left: 868px;  top: 50px; }
  .daisy-3 { left: 550px;  top: 338px; }
  .daisy-4 { left: 328px;  top: 767px; }
  .daisy-5 { left: 1042px; top: 711px; }
  .daisy-6 { left: 908px;  top: 1011px; }
  .daisy-7 { left: 164px;  top: 1035px; }

  .product-type {
    position: absolute;
    left: 0; right: 0;
    top: 472px;
    text-align: center;
    padding-left: 28px;
    font-family: "Barlow Condensed", sans-serif;
    font-style: italic;
    font-weight: 700;
    font-size: 60px;
    line-height: 1;
    letter-spacing: 1px;
    color: var(--title);
  }
  .product-name {
    position: absolute;
    left: 359px;
    top: 561px;
    width: 480px;
    height: 106px;
    border-radius: 34px;
    background: var(--pill);
    display: flex;
    align-items: center;
    justify-content: center;
    font-family: "Great Vibes", cursive;
    font-size: 68px;
    line-height: 1;
    color: var(--ink);
  }
  .ingredients {
    position: absolute;
    left: 0; right: 0;
    top: 1073px;
    text-align: center;
    font-family: "Roboto", sans-serif;
    font-weight: 400;
    font-size: 29px;
    line-height: 1;
    color: var(--ink);
  }
</style>
</head>
<body>
<div class="canvas">
  <div class="label"></div>

  <div class="art art--tulip" role="img" aria-label="Illustration einer rosa Tulpenblüte"></div>
  <div class="art art--sunflower" role="img" aria-label="Illustration einer gelben Sonnenblume"></div>
  <div class="art art--stem" role="img" aria-label="Petrolfarbener Blumenstiel mit Blatt"></div>
  <div class="art art--blossom" role="img" aria-label="Illustration einer rosa Blüte"></div>

  <div class="art art--bee bee-top" role="img" aria-label="Illustration einer Biene"></div>
  <div class="art art--bee bee-left" role="img" aria-label="Illustration einer Biene"></div>
  <div class="art art--bee bee-right" role="img" aria-label="Illustration einer Biene"></div>

  <div class="art art--daisy daisy-1" role="img" aria-label="Kleines Gänseblümchen"></div>
  <div class="art art--daisy daisy-2" role="img" aria-label="Kleines Gänseblümchen"></div>
  <div class="art art--daisy daisy-3" role="img" aria-label="Kleines Gänseblümchen"></div>
  <div class="art art--daisy daisy-4" role="img" aria-label="Kleines Gänseblümchen"></div>
  <div class="art art--daisy daisy-5" role="img" aria-label="Kleines Gänseblümchen"></div>
  <div class="art art--daisy daisy-6" role="img" aria-label="Kleines Gänseblümchen"></div>
  <div class="art art--daisy daisy-7" role="img" aria-label="Kleines Gänseblümchen"></div>

  <h1 class="product-type">OXYMEL</h1>
  <div class="product-name">Amber Meadow</div>
  <p class="ingredients">Blütenhonig, Apfelessig, Zitrone, Ingwer, Kurkuma</p>
</div>
</body>
</html>
```